Label or packaging Design for Hair Care Line

Dear Designer,
We are Pelvoro, a brand known for our premium hairstyling tools, and we are excited to expand into hair care. We are currently looking for a talented designer to create the label designs for our entire luxury hair care line.
This project is crucial in establishing our visual identity in the hair care market, and we aim to position ourselves alongside premium brands such as TKW, Fendrick Hair Atelier, and Morvi.
Project Scope
We need a cohesive label design for our hair care line, which includes:
5 products (e.g., shampoo, conditioner, hair oil, styling cream, and a hair mask).
The designs should include:
Front label: Highlighting the product name, key features, and branding.
Our goal is to achieve a design that communicates premium luxury with a touch of professionalism. Below are the specific guidelines to help you align with our vision:
Style and Inspiration
Think of brands like TKW, Fendrick Hair Atelier, and Morvi.
Luxury and Minimalism: Clean lines, sophisticated typography, and an elegant color palette.
Subtle femininity: premium finishes like metallic accents (gold, silver, or rose gold).
Brand Personality
Premium: Reflecting high quality and exclusivity.
Modern & Professional: Appealing to a refined, professional audience but also suitable for lifestyle-oriented customers.
Warm & Empowering: A brand that celebrates confidence and individuality.
Color Palette
Neutral tones like black, white, accented with metallics (gold or silver) for a luxurious feel.
Colors that feel timeless and elegant rather than trendy or overly bright.
Typography
Use clean, modern fonts (preferably sans-serif or serif for a refined look).
Clear and legible for all product details while maintaining a high-end aesthetic.
Materials and Finishes
Packaging Shape
The label designs should suit a variety of bottle and jar shapes (e.g., cylindrical, flat, or rounded).
Keep scalability in mind so the identity remains consistent across different products.
Deliverables
To understand the aesthetic we are aiming for, here are some brands to use as inspiration:
TKW: For its minimalistic and modern approach.
Fendrick Hair Atelier: For its combination of luxury and professional appeal.
Morvi: For its soft femininity and lifestyle branding.
we would like to see your designs applied to a variety of packaging types to get an overall impression of how the brand identity works across different product formats. This includes:
A squeeze bottle (e.g., for styling creams or conditioners).
A glass bottle with a dropper (e.g., for a luxurious hair oil).
A shampoo/conditioner bottle (standard pump or flip-top cap).
A spray bottle (e.g., for leave-in treatments or heat protectors).
By creating designs for these different packaging types, we can better evaluate how cohesive and versatile the brand identity will be across the entire product line.

Updates
As you may have noticed from the designs, they don’t quite align with our briefing. The look needs to be clean and professional, similar to Fendrick, TKW, and the other examples we provided. Please address this, and we’ll check it!

Target Market(s)
europe and us
Font styles to use
Other font styles liked:
- century gothic

Look and feel

```html
<!DOCTYPE html>
<html lang="en">
<head>
<meta charset="utf-8">
<title>Pelvoro Hair Care Label Set</title>
<link rel="stylesheet" href="https://fonts.googleapis.com/css2?family=Montserrat:wght@400;600&display=swap">
<style>
  :root {
    --sheet: #96b4d4;
    --navy: #272a38;
    --navy-soft: #343545;
    --gold: #dcb990;
    --gold-deep: #b89a74;
  }
  * { margin: 0; padding: 0; box-sizing: border-box; }
  html, body { width: 919px; height: 1200px; overflow: hidden; }
  body {
    position: relative;
    background: var(--sheet);
    font-family: "Montserrat", "Century Gothic", sans-serif;
  }
  .label {
    position: absolute;
    background: var(--navy);
    overflow: hidden;
  }
  .label__pattern {
    position: absolute;
    left: 0; top: 0; width: 100%;
    background:
      radial-gradient(ellipse at 30% 40%, rgba(220,185,144,0.22), transparent 60%),
      radial-gradient(ellipse at 75% 60%, rgba(220,185,144,0.18), transparent 60%),
      var(--navy-soft);
  }
  .label__band {
    position: absolute;
    left: 0; width: 100%;
    height: 4.4px;
    background: var(--gold);
  }
  .label__logo {
    position: absolute;
    background: var(--navy);
    border: 1.2px solid var(--gold);
    padding: 4px;
  }
  .label__logo-inner {
    width: 100%; height: 100%;
    background: var(--gold);
    display: flex; align-items: center; justify-content: center;
    color: var(--navy);
    font-weight: 400;
    font-size: 13px;
    letter-spacing: 0.3px;
  }
  .label__title {
    position: absolute;
    left: 0; width: 100%;
    text-align: center;
    color: var(--gold);
    font-weight: 600;
    font-size: 16px;
    letter-spacing: 0.6px;
    line-height: 1;
  }
  .label__copy {
    position: absolute;
    left: 0; width: 100%;
    text-align: center;
    color: var(--gold);
    font-size: 4.2px;
    line-height: 5.7px;
  }
  .label__foot {
    position: absolute;
    left: 0; width: 100%;
    height: 5px;
    background: var(--gold);
  }

  /* individual labels */
  .label--shampoo { left: 48.7px; top: 36.1px; width: 364.3px; height: 363.8px; }
  .label--conditioner { left: 453.5px; top: 40.5px; width: 416.3px; height: 359.9px; }
  .label--mask { left: 48.7px; top: 441.4px; width: 821.5px; height: 274px; }
  .label--styling { left: 48.7px; top: 765.3px; width: 392.2px; height: 339.1px; }
  .label--oil { left: 477.5px; top: 765.3px; width: 392.2px; height: 339.1px; }
</style>
</head>
<body>

<section class="label label--shampoo">
  <div class="label__pattern" style="height:180px" role="img" aria-label="Gold line pattern of interlocking wavy columns on navy"></div>
  <div class="label__band" style="top:180px"></div>
  <div class="label__logo" style="left:126.4px; top:148.2px; width:111px; height:67.3px">
    <div class="label__logo-inner">Pelvoro</div>
  </div>
  <h2 class="label__title" style="top:248.5px">SHAMPOO</h2>
  <p class="label__copy" style="top:310px">Gently cleanses hair and scalp with a rich, creamy lather<br>that lifts away buildup while keeping natural moisture and shine.<br>Suitable for all hair types and daily use.<br>Rinse well after use.</p>
  <div class="label__foot" style="top:343px"></div>
</section>

<section class="label label--conditioner">
  <div class="label__pattern" style="height:177.8px" role="img" aria-label="Gold line pattern of overlapping arches on navy"></div>
  <div class="label__band" style="top:177.8px"></div>
  <div class="label__logo" style="left:153.2px; top:146.6px; width:110px; height:66.7px">
    <div class="label__logo-inner">Pelvoro</div>
  </div>
  <h2 class="label__title" style="top:245px">CONDITIONER</h2>
  <p class="label__copy" style="top:305.8px">Smooths and detangles each strand with a light, silky finish<br>that restores softness and seals in lasting moisture and shine.<br>Apply to lengths after shampoo, leave for<br>two minutes, then rinse.</p>
  <div class="label__foot" style="top:338.6px"></div>
</section>

<section class="label label--mask">
  <div class="label__pattern" style="height:134.6px" role="img" aria-label="Gold art deco line pattern of linked arches and drops on navy"></div>
  <div class="label__band" style="top:134.6px"></div>
  <div class="label__logo" style="left:347.3px; top:99.6px; width:126.4px; height:76px">
    <div class="label__logo-inner" style="font-size:14px">Pelvoro</div>
  </div>
  <h2 class="label__title" style="top:216px; font-size:17.5px">HAIR MASK</h2>
  <div class="label__foot" style="top:269px"></div>
</section>

<section class="label label--styling">
  <div class="label__pattern" style="height:168px" role="img" aria-label="Sweeping gold line waves like flowing hair on navy"></div>
  <div class="label__band" style="top:168px"></div>
  <div class="label__logo" style="left:144.4px; top:138.4px; width:103.4px; height:62.4px">
    <div class="label__logo-inner">Pelvoro</div>
  </div>
  <h2 class="label__title" style="top:230.5px">STYLING CREAM</h2>
  <p class="label__copy" style="top:287.7px">Shapes and defines with a soft, flexible hold that tames<br>frizz and adds polish without weight or sticky residue.<br>Work a small amount through damp or dry<br>hair and style as desired.</p>
  <div class="label__foot" style="top:320px"></div>
</section>

<section class="label label--oil">
  <div class="label__pattern" style="height:168px" role="img" aria-label="Gold line pattern of swirling leaves and waves on navy"></div>
  <div class="label__band" style="top:168px"></div>
  <div class="label__logo" style="left:144.4px; top:138.4px; width:103.4px; height:62.4px">
    <div class="label__logo-inner">Pelvoro</div>
  </div>
  <h2 class="label__title" style="top:230.5px">HAIR OIL</h2>
  <p class="label__copy" style="top:287.7px">A weightless blend of precious oils that nourishes, softens<br>and protects hair from heat while adding a glossy finish.<br>Warm two drops in palms and smooth<br>through mid-lengths and ends.</p>
  <div class="label__foot" style="top:320px"></div>
</section>

</body>
</html>
```